Veltrix Saves Doctor! HTML BillBoard

I need a HTMl Page that is going to be emailed to Dr's, its about our service and they can push a button if they would like our salesmen to come see them,
The HTML Page should be designed to scare the Dr. so that they want to use our service right away! Use or logo colors plus others you like, this should read like a flyer, and know that doctors will only view for a few seconds before they decide. his project is going to be a 81/2 by 11 inch HTML Flyer that will be Emailed to Doctors
The Main Message is "Veltrix Protects Doctor"
then this:
Lets say Your Worst Case Scenario Happens… Your Patient Dies..... Now the Family Says..... "you got them addicted" and Sues the Practice!
Then This:
What's in Your Chart Right Now That is Protecting You?
Use the catch phrases I have supplied, these work the best for pain drs. please be creative with this project and have fun with it, I will work closely with you and will aide in your design, I have done a lot of projects with pixel harbor, so I am very familiar

Target Market(s)

Pain Management Doctors

Industry/Entity Type

Health Care

Coding

Coded - Design and coding required

Number of Pages Required

1 page

Font styles to use
Sans Serif

Colors
f37122
f8ba93
f78f20
faa54b
fac994

Requirements
Must have
• Must USE exact words I give you on the Document "Veltrix Protects Doctor" t, must look like a Flyer for our service,
• his project is going to be a 81/2 by 11 inch HTML Flyer that will be Emailed to Doctors
• The Main Message is "Veltrix Protects Doctor"
• then this:
• Lets say Your Worst Case Scenario Happens… Your Patient Dies..... Now the Family Says..... "you got them addicted" and Sues the Practice!
• Then This:
• What's in Your Chart Right Now That is Protecting You
Nice to have
• get creative, you can use other pictures along the same idea, chocolate browns and tans, aluminum grey for colors
Should not have
• any changes in our tag lines we provided you

```html
<!DOCTYPE html>
<html lang="en">
<head>
<meta charset="utf-8">
<title>Veltrix Protects Doctor</title>
<link href="https://fonts.googleapis.com/css2?family=Raleway:wght@400;600;700;800&family=Open+Sans:wght@400;600;700&display=swap" rel="stylesheet">
<style>
:root{
  --orange:#f37122;
  --orange-mid:#f78f20;
  --orange-light:#faa54b;
  --peach:#f8ba93;
  --sand:#fac994;
  --ink:#2c2c2c;
  --body:#6b6b6b;
  --panel:#eeeeee;
  --line:#dcdcdc;
  --white:#ffffff;
}
*{margin:0;padding:0;box-sizing:border-box}
html,body{width:1200px;height:3964px;overflow:hidden;background:var(--white)}
body{font-family:"Open Sans",Arial,sans-serif;color:var(--body);font-size:13px;line-height:1.55}
h1,h2,h3,h4,.brand,.btn{font-family:"Raleway",Arial,sans-serif}
.wrap{width:880px;margin:0 auto;position:relative;height:100%}
section,header,footer{position:relative}
.photo{display:block}
.btn{display:inline-block;background:var(--orange);color:var(--white);font-size:11px;font-weight:700;letter-spacing:.5px;text-transform:uppercase;padding:7px 16px;border-radius:2px}

/* header */
.site-header{height:88px;border-bottom:3px solid var(--orange)}
.site-header .wrap{display:flex;align-items:center;justify-content:space-between}
.brand{display:flex;align-items:center;gap:10px;font-size:30px;font-weight:700;color:var(--orange)}
.brand-dot{width:30px;height:30px;border-radius:50%;background:var(--orange)}
.site-header .btn{padding:10px 20px}

/* hero */
.hero{height:532px}
.hero .photo{width:1200px;height:532px;background:linear-gradient(120deg,#cfcfcf 0%,#f2f2f2 35%,#e6e6e6 60%,#9e1b5a 88%,#c4457f 100%)}

/* stats */
.stats{height:420px;padding-top:40px}
.stats .wrap{display:flex;gap:30px}
.stat{width:273px}
.stat .photo{height:160px;background:linear-gradient(135deg,#8a7a6a,#c9b8a4)}
.stat:nth-child(2) .photo{background:linear-gradient(135deg,#b9c6d4,#e9e1d6)}
.stat:nth-child(3) .photo{background:linear-gradient(135deg,#5c4e44,#a89886)}
.stat h3{font-size:16px;font-weight:600;color:var(--ink);line-height:1.35;margin:18px 0 10px;min-height:44px}
.stat p{font-size:11.5px;margin-bottom:16px}

/* protects panel */
.protects{height:360px;padding-top:32px}
.panel{background:var(--panel);height:308px;padding:36px 60px 0}
.panel h2{text-align:center;font-size:22px;font-weight:800;color:var(--ink);letter-spacing:.5px}
.panel .lead{text-align:center;font-size:14px;color:var(--body);margin:4px 0 30px}
.points{display:grid;grid-template-columns:1fr 1fr;column-gap:50px;row-gap:26px}
.point{display:flex;gap:18px}
.point-icon{flex:0 0 56px;height:56px;border-radius:50%;background:var(--orange);display:flex;align-items:center;justify-content:center}
.point h4{font-size:14px;font-weight:700;color:var(--ink);margin-bottom:4px}
.point p{font-size:11px;line-height:1.5}

/* chart */
.chart{height:320px;padding-top:36px}
.chart .wrap{display:flex;gap:40px}
.chart-copy{flex:1}
.chart h2{font-size:22px;font-weight:800;color:var(--ink)}
.chart .sub{font-size:15px;color:var(--ink);font-weight:600;margin-bottom:16px}
.chart .ask{color:var(--orange);font-size:15px;font-weight:600;margin-bottom:14px}
.chart-copy p{font-size:12px;margin-bottom:14px}
.chart-copy b{color:var(--ink)}
.chart .photo{width:300px;height:220px;background:linear-gradient(135deg,#c46a1c,#f2a24a 45%,#fbe3c2 70%,#d87a26)}

/* know */
.know{height:300px;padding-top:10px}
.know h2{text-align:center;font-size:20px;font-weight:800;color:var(--ink);margin-bottom:22px}
.know-row{display:flex;gap:18px}
.know-row .photo{flex:1;height:208px;background:linear-gradient(135deg,#7a6b5e,#cbbcac)}
.know-row .photo:nth-child(2){background:linear-gradient(135deg,#3b3b3b,#8d8d8d)}
.know-row .photo:nth-child(3){background:linear-gradient(135deg,#d9d6d0,#9b948b)}

/* video */
.video{height:510px;padding-top:28px}
.video .photo{height:462px;background:linear-gradient(180deg,#a7500f 0%,#e6892c 40%,#f6b35c 70%,#b85f18 100%);display:flex;align-items:center;justify-content:center}
.play{width:96px;height:96px;border-radius:50%;border:4px solid var(--white);background:rgba(0,0,0,.25);display:flex;align-items:center;justify-content:center}

/* fact blocks */
.fact{height:240px;padding-top:20px}
.fact.alt{height:250px}
.fact .wrap{display:flex;gap:36px}
.fact .photo{width:300px;height:200px;flex:0 0 300px;background:linear-gradient(135deg,#2f3a48,#8a98a8)}
.fact.alt .photo{background:linear-gradient(135deg,#f4f1ee,#c9c2bb)}
.fact h3{font-size:18px;font-weight:600;color:var(--ink);line-height:1.35;margin:6px 0 12px}
.fact p{font-size:11.5px}

/* band */
.band{height:480px;padding-top:28px}
.band-box{background:var(--orange-mid);height:432px;padding:120px 110px 0;text-align:center;color:var(--white)}
.band-box h2{font-size:22px;font-weight:800;line-height:1.4;text-transform:uppercase;letter-spacing:.5px}
.band-box p{font-size:12px;margin-top:22px;color:#fff3e6}

/* closing stats */
.closing{height:372px;padding-top:32px}
.closing .wrap{display:flex;gap:40px}
.closing-item{flex:1}
.closing-item .photo{height:160px;background:linear-gradient(135deg,#e9e3d6,#7b8a4e)}
.closing-item:nth-child(2) .photo{background:linear-gradient(135deg,#2a2623,#d08b34)}
.closing-item h3{font-size:16px;font-weight:600;color:var(--ink);margin:18px 0 8px;line-height:1.35}
.closing-item p{font-size:11.5px;margin-bottom:14px}

/* footer */
.site-footer{height:92px;background:var(--panel)}
.site-footer .wrap{display:flex;align-items:center;justify-content:space-between}
.site-footer .brand{font-size:26px}
.site-footer .brand-dot{width:26px;height:26px}
.legal{font-size:11px;color:var(--body)}
.social{display:flex;gap:8px}
.social span{width:26px;height:26px;border-radius:50%;border:2px solid #8a8a8a}
</style>
</head>
<body>

<header class="site-header">
  <div class="wrap">
    <div class="brand"><span class="brand-dot"></span>Veltrix</div>
    <span class="btn">Sign Up</span>
  </div>
</header>

<section class="hero">
  <div class="photo" role="img" aria-label="White pills spilling from a tipped-over prescription bottle"></div>
</section>

<section class="stats">
  <div class="wrap">
    <article class="stat">
      <div class="photo" role="img" aria-label="Worried patient holding a pill"></div>
      <h3>Were dependent on prescription opioids in 2014</h3>
      <p>Chronic pain patients often move from relief to reliance. Careful charting and counseling help protect the patient and your practice.</p>
      <span class="btn">Read More</span>
    </article>
    <article class="stat">
      <div class="photo" role="img" aria-label="Doctor consulting with a patient"></div>
      <h3>About 16 million people in the US abuse prescription medication</h3>
      <p>Misuse often begins with a valid prescription. Documented counseling shows you took every reasonable step to keep patients safe.</p>
      <span class="btn">Read More</span>
    </article>
    <article class="stat">
      <div class="photo" role="img" aria-label="Person in chronic pain lying down"></div>
      <h3>100,000,000 in chronic pain. How Many More Must Die?</h3>
      <p>Every patient on opioids is a risk you carry. A clear record of care is the best answer when questions come.</p>
      <span class="btn">Read More</span>
    </article>
  </div>
</section>

<section class="protects">
  <div class="wrap">
    <div class="panel">
      <h2>VELTRIX PROTECTS DOCTOR</h2>
      <p class="lead">Lets say Your Worst Case Scenario Happens…</p>
      <div class="points">
        <div class="point">
          <span class="point-icon"><svg width="26" height="26" viewBox="0 0 24 24"><circle cx="12" cy="8" r="4" fill="#fff"/><path d="M4 21c0-4.4 3.6-7 8-7s8 2.6 8 7z" fill="#fff"/></svg></span>
          <div><h4>Your Patient Dies</h4><p>Even with careful care, an overdose can happen. What your chart shows next decides how your practice is judged.</p></div>
        </div>
        <div class="point">
          <span class="point-icon"><svg width="26" height="26" viewBox="0 0 24 24"><path d="M3 5h18v11H9l-5 4v-4H3z" fill="#fff"/></svg></span>
          <div><h4>Now the Family Says</h4><p>Grieving families look for answers and someone to blame. Your prescribing history will be read line by line.</p></div>
        </div>
        <div class="point">
          <span class="point-icon"><svg width="26" height="26" viewBox="0 0 24 24"><path d="M2 11l20-8-8 20-3-9z" fill="#fff"/></svg></span>
          <div><h4>"You got them addicted"</h4><p>Without proof of counseling, it is your word against theirs. Addiction claims are hard to defend alone.</p></div>
        </div>
        <div class="point">
          <span class="point-icon"><svg width="26" height="26" viewBox="0 0 24 24"><rect x="3" y="7" width="18" height="13" rx="2" fill="#fff"/><rect x="9" y="4" width="6" height="4" fill="none" stroke="#fff" stroke-width="2"/></svg></span>
          <div><h4>and Sues the Practice!</h4><p>Legal costs, lost time and a damaged name follow a lawsuit. Veltrix helps you stand on solid records.</p></div>
        </div>
      </div>
    </div>
  </div>
</section>

<section class="chart">
  <div class="wrap">
    <div class="chart-copy">
      <h2>WHAT'S IN YOUR CHART RIGHT NOW</h2>
      <p class="sub">That is Protecting You?</p>
      <p class="ask">Can You afford NOT to use Veltrix ??</p>
      <p><b>Pro Active Addiction Counseling</b> helping your patients understand the risks of the medications you prescribe.</p>
      <p><b>Signatures of Understanding</b> show the patient was informed and accepted responsibility for safe use of their medication.</p>
    </div>
    <div class="photo" role="img" aria-label="Rows of orange prescription pill bottles"></div>
  </div>
</section>

<section class="know">
  <div class="wrap">
    <h2>HOW WELL DO YOU (DR.) KNOW YOUR PATIENT??</h2>
    <div class="know-row">
      <div class="photo" role="img" aria-label="Patient talking with a doctor"></div>
      <div class="photo" role="img" aria-label="Distressed person holding pills"></div>
      <div class="photo" role="img" aria-label="Person reaching for a medicine bottle"></div>
    </div>
  </div>
</section>

<section class="video">
  <div class="wrap">
    <div class="photo" role="img" aria-label="Video still of prescription bottles and pills">
      <span class="play"><svg width="40" height="40" viewBox="0 0 24 24"><path d="M8 5l12 7-12 7z" fill="#fff"/></svg></span>
    </div>
  </div>
</section>

<section class="fact">
  <div class="wrap">
    <div class="photo" role="img" aria-label="Hands holding a handful of pills"></div>
    <div>
      <h3>Drug overdose is the leading cause of accidental death in the US, with 47,055 lethal drug overdoses in 2014</h3>
      <p>Overdose deaths have risen every year for more than a decade, and prescription painkillers are part of the story. Pain doctors sit at the center of this problem, balancing real suffering against the risk of misuse. A documented counseling program shows that every patient was warned, educated and supported.</p>
    </div>
  </div>
</section>

<section class="fact alt">
  <div class="wrap">
    <div>
      <h3>Every day, over 1800 people are treated in emergency departments for misusing prescription opioids</h3>
      <p>Emergency visits tied to opioid misuse keep climbing, and each one can lead back to a prescriber. When a case reaches a courtroom, the first question is simple: what did the doctor do to prevent this? Veltrix puts that answer in your chart.</p>
    </div>
    <div class="photo" role="img" aria-label="Open hand with spilled pills on a white surface"></div>
  </div>
</section>

<section class="band">
  <div class="wrap">
    <div class="band-box">
      <h2>Patients can sue doctors can you<br>afford not to have Veltrix in your charts</h2>
      <p>Our counselors meet your patients, explain the risks of their medication and record every session, so your practice has the proof it needs when it matters most.</p>
    </div>
  </div>
</section>

<section class="closing">
  <div class="wrap">
    <article class="closing-item">
      <div class="photo" role="img" aria-label="Pills and herbs on a white table"></div>
      <h3>Each day, 78 people die from an overdose of prescription painkillers in the US</h3>
      <p>Most of these deaths began with a legal prescription. Clear counseling records show you acted with care and followed every safe step.</p>
      <span class="btn">Read More</span>
    </article>
    <article class="closing-item">
      <div class="photo" role="img" aria-label="Tipped prescription bottle with pills"></div>
      <h3>1 death every 19 mins</h3>
      <p>While you read this page, another family lost someone. Make sure your chart tells the full story of the care you gave.</p>
      <span class="btn">Read More</span>
    </article>
  </div>
</section>

<footer class="site-footer">
  <div class="wrap">
    <div class="brand"><span class="brand-dot"></span>Veltrix</div>
    <p class="legal">© 2016 All Rights Reserved. Terms of Use. Privacy Policy</p>
    <div class="social"><span></span><span></span><span></span><span></span><span></span></div>
  </div>
</footer>

</body>
</html>
```